Design and Renovation Company Luxury Business Card

I want to create a luxury business card for a Design and Renovation Firm . We will use our current logo. The company name is 528BUILDA. We do not want anything standard. We need a very unique concept.
Please see uploaded inspiration. I really like the textured paper option. I would like the card to be thick with debossing, and/or embossing options. The logo has orange in it but I would like to see the card with and without the orange. I think the orange may make the company feel less high-end. The goal is to elevate the logo not match its vibe per se of the logo. We want something very unique, not standard at all!
I would like a space for :
Logo,
Name,
Position,
Email,
Office number,
Website Address,
Business Address,
Thank you!
Have fun!
Target Market(s)
Home owners Age 35 +
Industry/Entity Type
Design and Renovation
Contact Information for Business Card
Logo, Name, Position, Email, Office number, Website Address, Business Address,.
Colors
Designer to choose colors to be used in the design.
Requirements
Must have
- A luxury designer feel. Must be black or dark grey but open to other luxury ideas.
Nice to have
- Gold, silver, black embossing or debossing. Textured paper design.
Should not have
- A cheap look and feel.

```html
<!DOCTYPE html>
<html lang="en">
<head>
<meta charset="utf-8">
<title>528BUILDA Business Card</title>
<link href="https://fonts.googleapis.com/css2?family=Saira:wght@400&family=Roboto:wght@400;700&display=swap" rel="stylesheet">
<style>
  :root {
    --backdrop: #3a3a3b;
    --card: #2b2b2c;
    --card-edge: #1e1e1f;
    --deboss: #4a4a4c;
    --white: #f2f2f2;
    --orange: #f7931e;
    --rule: #5a5a5c;
  }
  * { margin: 0; padding: 0; box-sizing: border-box; }
  html, body { width: 1200px; height: 689px; overflow: hidden; }
  body {
    background: var(--backdrop);
    position: relative;
    font-family: "Roboto", Arial, sans-serif;
  }
  .card {
    position: absolute;
    top: 190px;
    width: 540px;
    height: 309px;
    background: var(--card);
    border-radius: 16px;
    border: 1px solid var(--card-edge);
  }
  .card--front { left: 40px; }
  .card--back { left: 620px; }

  .brand {
    position: absolute;
    display: flex;
    align-items: center;
    justify-content: center;
    font-family: "Saira", Arial, sans-serif;
    font-weight: 400;
    line-height: 1;
    letter-spacing: 2px;
  }
  .card--front .brand {
    inset: 0;
    font-size: 58px;
    color: var(--deboss);
  }
  .card--back .brand {
    left: 20px; top: 0; bottom: 0; width: 250px;
    font-size: 34px;
    color: var(--white);
  }

  .divider {
    position: absolute; left: 290px; top: 40px; bottom: 40px;
    width: 1px; background: var(--rule);
  }
  .contact {
    position: absolute; left: 316px; top: 62px; width: 210px;
    color: var(--white);
  }
  .contact__name { color: var(--orange); font-weight: 700; font-size: 18px; letter-spacing: 0.5px; }
  .contact__role { font-size: 12px; margin-bottom: 18px; }
  .contact__address { font-size: 12px; line-height: 1.45; margin-bottom: 14px; }
  .contact__list { list-style: none; font-size: 12px; line-height: 1.6; }
  .contact__list li { display: flex; align-items: center; gap: 8px; }
  .icon { width: 11px; height: 11px; flex: none; }
</style>
</head>
<body>
  <section class="card card--front" aria-label="Card front">
    <p class="brand">528BUILDA</p>
  </section>

  <section class="card card--back" aria-label="Card back">
    <p class="brand">528BUILDA</p>

    <div class="divider"></div>

    <div class="contact">
      <p class="contact__name">MARCUS HALE</p>
      <p class="contact__role">President</p>
      <p class="contact__address">4215 Linden Court<br>Halifax, Canada 20816</p>
      <ul class="contact__list">
        <li>
          <svg class="icon" viewBox="0 0 24 24"><path fill="#f7931e" d="M6.6 10.8a15.1 15.1 0 0 0 6.6 6.6l2.2-2.2a1 1 0 0 1 1-.25 11.4 11.4 0 0 0 3.6.57 1 1 0 0 1 1 1V20a1 1 0 0 1-1 1A17 17 0 0 1 3 4a1 1 0 0 1 1-1h3.5a1 1 0 0 1 1 1c0 1.25.2 2.45.57 3.57a1 1 0 0 1-.25 1z"/></svg>
          418-592-6031
        </li>
        <li>
          <svg class="icon" viewBox="0 0 24 24"><rect x="2" y="5" width="20" height="14" fill="#f7931e"/><path d="M2 5l10 8 10-8" fill="none" stroke="#2b2b2c" stroke-width="2"/></svg>
          info@528builda.com
        </li>
        <li>
          <svg class="icon" viewBox="0 0 24 24"><circle cx="12" cy="12" r="10" fill="#f7931e"/><path d="M2 12h20M12 2c3 3 3 17 0 20M12 2c-3 3-3 17 0 20" fill="none" stroke="#2b2b2c" stroke-width="1.5"/></svg>
          www.528builda.com
        </li>
      </ul>
    </div>
  </section>
</body>
</html>
```